Business Card Design

IT Solutions company.

I need a professional looking design with my company logo if possible.

Logo is located here:
http://www.brunelwavesystems.co.uk/dev/images/logo1.jpg
Feel free to redesign the logo if you think you have any better suggestions.

Our services include, IT Infrastructure/Telephony Maintenance & Hosting Services. Linux and Windows Solutions, App Development.

Out website is currently under development:
http://www.brunelwavesystems.co.uk/dev/

I'm looking for a colourful but professional looking business card.

Industry/Entity Type

Business

Contact Information for Business Card

BW Brunel Wavesystems Ltd
Martin Hollisby
07700958312
www.brunelwavesystems.co.uk
mhollisby@brunelwavesystems.co.uk

```html
<!DOCTYPE html>
<html lang="en">
<head>
<meta charset="utf-8">
<title>Brunel Wavesystems – Business Card</title>
<link rel="stylesheet" href="https://fonts.googleapis.com/css2?family=Open+Sans:wght@400;600;700&family=Arimo:wght@400;700&display=swap">
<style>
  :root {
    --stage: #e7e7e9;
    --card-white: #ffffff;
    --brand-blue: #1d4fe6;
    --ink: #2b2b2b;
    --ink-soft: #555555;
    --charcoal: #333333;
    --rule: #c9c9c9;
    --on-blue: #ffffff;
  }
  * { box-sizing: border-box; margin: 0; padding: 0; }
  html, body { width: 1200px; height: 486px; overflow: hidden; }
  body {
    background: var(--stage);
    font-family: "Open Sans", Arial, sans-serif;
    position: relative;
  }
  .card {
    position: absolute;
    top: 98px;
    width: 520px;
    height: 290px;
    overflow: hidden;
    box-shadow: 0 6px 18px rgba(0,0,0,.18);
  }

  /* Front */
  .card--front { left: 45px; background: var(--card-white); }
  .brand {
    position: absolute;
    display: flex;
    align-items: center;
    gap: 12px;
    white-space: nowrap;
  }
  .brand__dot {
    width: 46px; height: 46px; border-radius: 50%;
    background: var(--brand-blue);
    flex: none;
  }
  .brand__name {
    font-family: "Arimo", Arial, sans-serif;
    font-weight: 700;
    font-size: 24px;
    letter-spacing: .2px;
  }
  .card--front .brand { top: 50px; left: 0; right: 0; justify-content: center; }
  .card--front .brand__name { color: var(--ink); }

  .holder {
    position: absolute;
    left: 40px; top: 178px;
    font-weight: 700;
    font-size: 19px;
    color: var(--brand-blue);
  }
  .divider {
    position: absolute;
    left: 252px; top: 148px;
    width: 1px; height: 70px;
    background: var(--rule);
  }
  .contacts {
    position: absolute;
    left: 262px; top: 150px;
    list-style: none;
    font-size: 13.5px;
    color: var(--ink);
  }
  .contacts li { display: flex; align-items: center; gap: 6px; height: 21px; }
  .contacts svg { width: 12px; height: 12px; flex: none; }
  .bands { position: absolute; left: 0; bottom: 0; width: 520px; height: 60px; }

  /* Back */
  .card--back { left: 635px; background: var(--brand-blue); color: var(--on-blue); text-align: center; }
  .card--back .brand { top: 44px; left: 0; right: 0; justify-content: center; }
  .card--back .brand__dot { background: var(--on-blue); }
  .card--back .brand__name { color: var(--on-blue); }
  .site {
    position: absolute; top: 112px; left: 0; right: 0;
    font-family: "Arimo", Arial, sans-serif;
    font-weight: 700; font-size: 14px; letter-spacing: .3px;
  }
  .services-title {
    position: absolute; top: 148px; left: 0; right: 0;
    font-family: "Arimo", Arial, sans-serif;
    font-weight: 700; font-size: 13.5px;
  }
  .services-rule {
    position: absolute; top: 170px; left: 160px; width: 200px; height: 1px;
    background: linear-gradient(90deg, transparent, var(--on-blue) 20%, var(--on-blue) 80%, transparent);
  }
  .services {
    position: absolute; top: 180px; left: 0; right: 0;
    list-style: none;
    font-family: "Arimo", Arial, sans-serif;
    font-weight: 700; font-size: 14px; line-height: 22px;
  }
  .services li::before { content: "• "; }
</style>
</head>
<body>

<section class="card card--front" aria-label="Business card front">
  <div class="brand">
    <span class="brand__dot"></span>
    <span class="brand__name">BW Brunel Wavesystems Ltd</span>
  </div>

  <p class="holder">Martin Hollisby</p>
  <span class="divider"></span>

  <ul class="contacts">
    <li>
      <svg viewBox="0 0 12 12" aria-hidden="true"><circle cx="6" cy="6" r="5.4" fill="none" stroke="#2b2b2b" stroke-width="1"/><path d="M4.2 3.2 5.2 3 5.6 4.6 5 5.1c.3.8.8 1.4 1.6 1.8l.6-.5 1.5.6-.2 1C6.2 8.5 3.8 6 4.2 3.2z" fill="#2b2b2b"/></svg>
      07700958312
    </li>
    <li>
      <svg viewBox="0 0 12 12" aria-hidden="true"><rect x="1" y="3" width="10" height="7" rx="1" fill="#2b2b2b"/><path d="M1.5 3.5 6 7l4.5-3.5" fill="none" stroke="#fff" stroke-width="1"/></svg>
      mhollisby@brunelwavesystems.co.uk
    </li>
    <li>
      <svg viewBox="0 0 12 12" aria-hidden="true"><circle cx="6" cy="6" r="5.2" fill="#2b2b2b"/><path d="M1 6h10M6 .8v10.4M3.3 2.2c1.6 2.3 1.6 5.3 0 7.6M8.7 2.2c-1.6 2.3-1.6 5.3 0 7.6" fill="none" stroke="#fff" stroke-width=".8"/></svg>
      www.brunelwavesystems.co.uk
    </li>
  </ul>

  <svg class="bands" viewBox="0 0 520 60" aria-hidden="true">
    <polygon points="270,40 520,2 520,60 250,60" fill="var(--brand-blue)"/>
    <polygon points="0,46 262,40 242,60 0,60" fill="var(--charcoal)"/>
  </svg>
</section>

<section class="card card--back" aria-label="Business card back">
  <div class="brand">
    <span class="brand__dot"></span>
    <span class="brand__name">BW Brunel Wavesystems Ltd</span>
  </div>
  <p class="site">www.brunelwavesystems.co.uk</p>
  <p class="services-title">Our Services Include</p>
  <span class="services-rule"></span>
  <ul class="services">
    <li>IT Infrastructure/Telephony Maintenance</li>
    <li>Hosting Services</li>
    <li>Linux and Windows Solutions</li>
    <li>App Development</li>
  </ul>
</section>

</body>
</html>
```